New Company Business Card design

Looking for a corporate looking business card utilising my new logo design - the logo i would like embossed as one option and flat as another - simplistic but stylish - less is more - we are an import export business launching into the market - i would like a couple of options as main background - Grey or Black

```html
<!DOCTYPE html>
<html lang="en">
<head>
<meta charset="utf-8">
<title>Meridian Trade Partners – Business Card</title>
<link href="https://fonts.googleapis.com/css2?family=Cinzel:wght@500&family=Oswald:wght@600&family=Work+Sans:wght@400&display=swap" rel="stylesheet">
<style>
  :root {
    --backdrop: #1c1c1d;
    --card: #161617;
    --card-edge: #232325;
    --silver: #b9b9bb;
    --ink-deep: #0b0b0b;
    --muted: #6d6d70;
    --text-light: #c9c9cb;
  }
  * { margin: 0; padding: 0; box-sizing: border-box; }
  html, body {
    width: 1200px; height: 900px; overflow: hidden;
    background: var(--backdrop);
  }
  .canvas {
    position: relative; width: 1200px; height: 900px;
    display: flex; flex-direction: column; align-items: center;
    justify-content: center; gap: 56px;
  }
  .card {
    position: relative; width: 620px; height: 354px;
    background: var(--card);
    border: 1px solid var(--card-edge);
  }
  /* Front */
  .card-front {
    display: flex; align-items: center; justify-content: center; gap: 16px;
  }
  .brand-dot {
    width: 22px; height: 22px; border-radius: 50%;
    background: var(--silver);
  }
  .brand-name {
    font-family: "Cinzel", serif; font-weight: 500;
    font-size: 26px; letter-spacing: 2px; color: var(--silver);
  }
  /* Back */
  .card-back { font-family: "Work Sans", sans-serif; }
  .identity {
    position: absolute; left: 70px; top: 128px; width: 200px; text-align: right;
  }
  .person-name {
    font-family: "Oswald", sans-serif; font-weight: 600;
    font-size: 30px; letter-spacing: 1px; color: var(--ink-deep);
    text-transform: uppercase; line-height: 1.1;
  }
  .person-role { font-size: 14px; color: var(--muted); margin-top: 2px; }
  .divider {
    position: absolute; left: 290px; top: 132px;
    width: 1px; height: 64px; background: var(--muted);
  }
  .contact-list {
    position: absolute; left: 310px; top: 128px; list-style: none;
  }
  .contact-list li {
    display: flex; align-items: center; gap: 10px;
    font-size: 15px; letter-spacing: 0.5px; color: var(--text-light);
    height: 24px;
  }
  .contact-list svg { width: 12px; height: 12px; fill: none; stroke: var(--muted); stroke-width: 1.5; }
  .address {
    position: absolute; left: 70px; bottom: 56px;
    font-size: 15px; letter-spacing: 0.5px; color: var(--text-light);
  }
</style>
</head>
<body>
<main class="canvas">
  <section class="card card-front" aria-label="Card front">
    <span class="brand-dot"></span>
    <span class="brand-name">Meridian Trade Partners</span>
  </section>

  <section class="card card-back" aria-label="Card back">
    <div class="identity">
      <p class="person-name">Daniel Hart</p>
      <p class="person-role">Director</p>
    </div>
    <span class="divider"></span>
    <ul class="contact-list">
      <li>
        <svg viewBox="0 0 12 12"><path d="M2.5 1.5l2 0.2 0.8 2.2-1.2 0.9a6 6 0 0 0 3.1 3.1l0.9-1.2 2.2 0.8 0.2 2a1 1 0 0 1-1 1A8.5 8.5 0 0 1 1.5 2.5a1 1 0 0 1 1-1z"/></svg>
        555-014-2280
      </li>
      <li>
        <svg viewBox="0 0 12 12"><rect x="1" y="2.5" width="10" height="7"/><path d="M1 2.5l5 4 5-4"/></svg>
        hello@meridiantrade.com
      </li>
      <li>
        <svg viewBox="0 0 12 12"><circle cx="6" cy="6" r="5"/><ellipse cx="6" cy="6" rx="2.2" ry="5"/><path d="M1 6h10"/></svg>
        www.meridiantrade.com
      </li>
    </ul>
    <p class="address">2750 Harbor View Ave Fairview, CA 94100-2210</p>
  </section>
</main>
</body>
</html>
```